Bright Harbor, LLC Business Card Design

We need a product business card designed for a new company Bright Harbor, LLC. We make and resell waterless RV cleaner, polish and protectant. It cleans and protects in a simple spray and wipe step leaving the surface protected and conditioned to repel dust, dirt, water, smudges, bugs and fingerprints while preventing fogging. Safe on acrylic, plexiglas, lexan, plastic, rubber, painted surfaces, chrome, stainless, aluminum, vinyl, leather, glass.... This is an eco-friendly green product.

We want to play off the company name to tell the consumer that the product is easy to use and associate to the nostalgics 1950's in the USA... Thinking old travel trailer with hot rod truck pulling it as the graphic, maybe the husband cleaning the truck and the wife cleaning the trailer for a Bright Harbor surface.
Updates

Just posted our newly finished logo. Need to have "Cleaner and Protectant" added to the design as well. Thanks everyone that has submitted thus far, i am working to get comments on all.

If you need a different file format, please let me know. Thank you.

Most important info, is the logo, website and the words "Cleaner" or "Clean" along "Protectant" or "Protect" the remainder is of less importance. Highlight: www.brightharborwash.example Focus is on company brand for Brighter Harbor Cleaner product: However, need a section for the following contact info: Walt Ferris (xxx) xxx-xxxx email address Would like space for QR Code if possible.

Target Market(s)

Adults in the USA between ages of 35-75 that are actively involved in the Recreational Vehicle (RV), travel trailer, and hot rod lifestyle. We are targeting the RV marked of the high end travel, 5th wheel and bus RV market. Along with hot rods, automotive and motorcycle market.

Industry/Entity Type

Travel

Requirements
Must have
• Most important info, is the logo, website and the words "Cleaner" or "Clean" along "Protectant" or "Protect" the remainder is of less importance.

Highlight:
www.brightharborwash.example

Focus is on company brand for Brighter Harbor Cleaner product: However, need a section for the following contact info:

Walt Ferris
(xxx) xxx-xxxx
email address
Nice to have
• Would like a space for a QR Code.

```html
<!DOCTYPE html>
<html lang="en">
<head>
<meta charset="utf-8">
<title>Bright Harbor — Business Card</title>
<link rel="stylesheet" href="https://fonts.googleapis.com/css2?family=Ubuntu:wght@400;500;700&display=swap">
<style>
  :root {
    --stage: #ecebe8;
    --card-white: #ffffff;
    --card-orange: #f15a3a;
    --sweep-grey: #5d5d60;
    --sweep-light: #9a9a9d;
    --ink-dark: #3a3a3c;
    --ink-soft: #6b6b6e;
    --ink-light: #ffffff;
  }
  * { box-sizing: border-box; margin: 0; padding: 0; }
  html, body {
    width: 1200px; height: 870px; overflow: hidden;
    background: var(--stage);
    font-family: "Ubuntu", sans-serif;
  }
  .stage {
    width: 1200px; height: 870px;
    display: flex; align-items: center; justify-content: center; gap: 40px;
  }
  .card {
    position: relative;
    width: 540px; height: 309px;
    overflow: hidden;
    box-shadow: 0 6px 18px rgba(0,0,0,0.18);
  }
  /* Front */
  .card-front { background: var(--card-white); }
  .card-front .sweep { position: absolute; inset: 0; width: 100%; height: 100%; }
  .brand { position: absolute; left: 48px; bottom: 48px; }
  .brand-name {
    font-weight: 700; font-size: 30px; letter-spacing: 1px;
    text-transform: uppercase; color: var(--ink-dark);
  }
  .brand-tagline {
    margin-top: 6px;
    font-weight: 500; font-size: 14px; letter-spacing: 2.5px;
    text-transform: uppercase; color: var(--card-orange);
  }
  /* Back */
  .card-back { background: var(--card-orange); color: var(--ink-light); }
  .holder { position: absolute; left: 36px; top: 30px; }
  .holder-name { font-size: 22px; font-weight: 400; letter-spacing: 1px; text-transform: uppercase; }
  .holder-role { font-size: 15px; margin-top: 4px; padding-left: 40px; }
  .contact {
    position: absolute; right: 30px; top: 104px;
    list-style: none; text-align: right; font-size: 14px; line-height: 1.5;
  }
  .contact .address { margin-bottom: 16px; line-height: 1.35; }
  .contact li { display: flex; justify-content: flex-end; align-items: center; gap: 8px; }
  .contact svg { width: 13px; height: 13px; flex: none; }
  .contact .icon-gap { width: 13px; flex: none; }
  .contact .website {
    margin-top: 10px; padding-top: 8px;
    border-top: 1px solid rgba(255,255,255,0.6);
    font-size: 17px; font-weight: 700; letter-spacing: 0.3px;
  }
  .contact .website svg { width: 15px; height: 15px; }
</style>
</head>
<body>
<main class="stage">
  <section class="card card-front" aria-label="Card front">
    <svg class="sweep" viewBox="0 0 540 309" preserveAspectRatio="none" aria-hidden="true">
      <path d="M388 0 C 440 70, 440 200, 400 309 L540 309 L540 0 Z" fill="var(--sweep-light)"/>
      <path d="M402 0 C 456 70, 456 200, 416 309 L540 309 L540 0 Z" fill="var(--sweep-grey)"/>
      <path d="M414 0 C 470 70, 470 200, 430 309 L540 309 L540 0 Z" fill="var(--card-orange)"/>
    </svg>
    <div class="brand">
      <p class="brand-name">Bright Harbor</p>
      <p class="brand-tagline">Cleaner &amp; Protectant</p>
    </div>
  </section>

  <section class="card card-back" aria-label="Card back">
    <div class="holder">
      <h1 class="holder-name">Walt Ferris</h1>
      <p class="holder-role">Managing Director</p>
    </div>
    <ul class="contact">
      <li class="address"><span>214 Harbor Lane, Suite 5<br>Dockside Road, BHW</span><span class="icon-gap"></span></li>
      <li><span>012 555 0148</span>
        <svg viewBox="0 0 16 16" aria-hidden="true"><path d="M4 1h3l1 4-2 1c1 2 2 3 4 4l1-2 4 1v3c0 1-1 2-2 2C6 14 2 10 2 3c0-1 1-2 2-2z" fill="currentColor"/></svg></li>
      <li><span>012 555 0148</span>
        <svg viewBox="0 0 16 16" aria-hidden="true"><rect x="4" y="1" width="8" height="14" rx="1.5" fill="none" stroke="currentColor" stroke-width="1.6"/><circle cx="8" cy="12.5" r="0.9" fill="currentColor"/></svg></li>
      <li><span>012 555 0148</span>
        <svg viewBox="0 0 16 16" aria-hidden="true"><rect x="2" y="6" width="12" height="7" fill="currentColor"/><rect x="4" y="2" width="8" height="4" fill="currentColor"/></svg></li>
      <li><span>walt@brightharbor.example</span>
        <svg viewBox="0 0 16 16" aria-hidden="true"><rect x="1" y="3" width="14" height="10" fill="currentColor"/><path d="M1 3l7 6 7-6" fill="none" stroke="var(--card-orange)" stroke-width="1.4"/></svg></li>
      <li class="website"><span>www.brightharborwash.example</span>
        <svg viewBox="0 0 16 16" aria-hidden="true"><circle cx="8" cy="8" r="6.5" fill="none" stroke="currentColor" stroke-width="1.4"/><ellipse cx="8" cy="8" rx="3" ry="6.5" fill="none" stroke="currentColor" stroke-width="1.2"/><path d="M1.5 8h13" stroke="currentColor" stroke-width="1.2"/></svg></li>
    </ul>
  </section>
</main>
</body>
</html>
```